New Business card design to reflect rebrand

I would like a business card design with a good base colour for our new logo and also a placeholder for a profile pic of the card holder. the design needs to be editable to the point that we can easily change the picture of the person and use that design for printmerlo etc. we are looking at a metalic finish business card so will need a good base colour to bring out the finish.

Target Market(s)

prospective customers

Industry/Entity Type

Business

Contact Information for Business Card

I would like one editable design that we can change the name of the card holder and profile picture. The design need to be in a format that be send to printmerlo etc.

Our address is Fenwick Lodge, Copse Lane, Ashcombe Wick, GU14 3TP Tel no. 01483 556172

Requirements
Must have
• place holder for a profile pic for the card holder. in AI or preferably PSD format

```html
<!DOCTYPE html>
<html lang="en">
<head>
<meta charset="utf-8">
<title>Corvane Workplace Services – Business Card</title>
<link rel="stylesheet" href="https://fonts.googleapis.com/css2?family=Michroma&family=Lato:wght@400&family=Montserrat:wght@600&display=swap">
<style>
  :root {
    --page-bg: #e9e7e4;
    --card-light: #f4f2f1;
    --card-dark: #1e1f2a;
    --brand-slate: #3f566f;
    --brand-orange: #ef6a1c;
    --text-light: #ffffff;
    --photo-top: #cfd3d8;
    --photo-bottom: #2a2f45;
  }
  html, body {
    margin: 0;
    width: 1200px;
    height: 900px;
    overflow: hidden;
    background: var(--page-bg);
  }
  .business-card {
    position: absolute;
    left: 150px;
    top: 172px;
    width: 900px;
    height: 555px;
    overflow: hidden;
    box-shadow: 0 10px 30px rgba(0,0,0,0.18);
  }
  .card-header {
    position: absolute;
    left: 0; top: 0;
    width: 900px;
    height: 310px;
    background: var(--card-light);
  }
  .profile-photo {
    position: absolute;
    left: 0; top: 0;
    width: 280px;
    height: 310px;
    background: linear-gradient(180deg, var(--photo-top) 0%, #9aa0ab 45%, var(--photo-bottom) 100%);
  }
  .brand {
    position: absolute;
    left: 330px;
    top: 88px;
    width: 490px;
    display: flex;
    align-items: center;
    justify-content: center;
    gap: 18px;
    font-family: "Montserrat", sans-serif;
    font-weight: 600;
    color: var(--brand-slate);
  }
  .brand-mark {
    width: 22px;
    height: 22px;
    border-radius: 50%;
    background: var(--brand-orange);
    flex: none;
  }
  .brand-name {
    text-align: center;
    line-height: 1;
  }
  .brand-name .brand-word {
    display: block;
    font-size: 64px;
    letter-spacing: 2px;
  }
  .brand-name .brand-tagline {
    display: block;
    margin-top: 14px;
    font-size: 22px;
    letter-spacing: 4px;
  }
  .card-details {
    position: absolute;
    left: 0; top: 310px;
    width: 900px;
    height: 245px;
    background: var(--card-dark);
    color: var(--text-light);
    text-align: center;
  }
  .holder-name {
    margin: 22px 0 6px;
    font-family: "Michroma", sans-serif;
    font-size: 29px;
    line-height: 40px;
    font-weight: 400;
    letter-spacing: 1px;
  }
  .contact-list {
    margin: 0;
    padding: 0;
    list-style: none;
    font-family: "Lato", sans-serif;
    font-size: 23px;
    line-height: 33px;
  }
</style>
</head>
<body>
  <div class="business-card">
    <div class="card-header">
      <div class="profile-photo" role="img" aria-label="Profile photo placeholder for the card holder"></div>
      <div class="brand">
        <span class="brand-mark"></span>
        <div class="brand-name">
          <span class="brand-word">CORVANE</span>
          <span class="brand-tagline">WORKPLACE SERVICES</span>
        </div>
      </div>
    </div>
    <div class="card-details">
      <h1 class="holder-name">DANIEL HARTWELL</h1>
      <ul class="contact-list">
        <li class="contact-phone">01483 556172</li>
        <li class="contact-email">info@corvane.com</li>
        <li class="contact-address">Fenwick Lodge, Copse Lane</li>
        <li class="contact-address">Ashcombe Wick, GU14 3TP</li>
      </ul>
    </div>
  </div>
</body>
</html>
```